Tovella Fireworks needs a web design and logo

We need a web design and logo for a fireworks business in Sydney Australia, we do public display, weddings, tv, theatrical, clubs and any other organisation that wants to do something special.
Name is Marrowind Fireworks & Pyrotechnics

```html
<!DOCTYPE html>
<html lang="en">
<head>
<meta charset="utf-8">
<title>Marrowind Fireworks &amp; Pyrotechnics</title>
<link rel="stylesheet" href="https://fonts.googleapis.com/css2?family=Raleway:wght@300;400;600;700;800&display=swap">
<style>
:root{
  --red:#d7141a;
  --dark:#141414;
  --header:#1b1b1b;
  --nav:#232323;
  --white:#ffffff;
  --grey:#e6e6e6;
  --muted:#9a9a9a;
  --text:#4a4a4a;
}
*{margin:0;padding:0;box-sizing:border-box}
html,body{width:853px;height:1200px;overflow:hidden;background:var(--white)}
body{font-family:"Raleway",sans-serif;position:relative}
.page{position:relative;width:853px;height:1200px}

.site-header{position:absolute;top:0;left:0;width:853px;height:90px;background:var(--header)}
.brand{position:absolute;left:34px;top:12px;color:var(--white);font-weight:600;letter-spacing:1px}
.brand-name{font-size:34px;line-height:38px;font-weight:600}
.brand-tag{font-size:11px;letter-spacing:2px;font-weight:600}
.search{position:absolute;left:612px;top:18px;width:120px;height:22px;background:#2d2d2d;color:var(--muted);font-size:9px;padding:6px 8px;letter-spacing:1px}
.cart{position:absolute;left:745px;top:20px;color:var(--red);font-size:9px;font-weight:700;letter-spacing:.5px;display:flex;align-items:center;gap:5px}
.social{position:absolute;top:50px;display:flex;gap:10px}
.social span{display:block;width:22px;height:22px;background:#2d2d2d}
.site-header .social{left:716px}

.main-nav{position:absolute;top:90px;left:0;width:853px;height:24px;background:var(--nav);display:flex;padding-left:28px}
.main-nav a{color:#cfcfcf;font-size:9px;font-weight:600;text-decoration:none;line-height:24px;padding:0 13px;letter-spacing:.5px}
.main-nav a.active{background:var(--red);color:var(--white)}

.hero{position:absolute;top:114px;left:0;width:853px;height:291px;background:linear-gradient(180deg,#7a2a5c 0%,#4a1a4c 50%,#1a0c1e 100%)}
.hero-title{position:absolute;top:96px;width:100%;text-align:center;color:var(--white);font-size:27px;font-weight:700;letter-spacing:.5px}
.hero-text{position:absolute;top:138px;left:250px;width:353px;text-align:center;color:#e8dce6;font-size:10px;line-height:14px}
.btn-outline{position:absolute;top:186px;left:386px;width:82px;height:26px;border:1.5px solid var(--white);color:var(--white);font-size:9px;font-weight:700;text-align:center;line-height:23px;letter-spacing:1px}
.hero-arrow{position:absolute;top:135px}

.promo-band{position:absolute;top:405px;left:0;width:853px;height:180px;background:var(--grey)}
.promo{position:absolute;top:428px;width:232px;height:155px;color:var(--white)}
.promo-1{left:71px;background:#1c1c1c;border:4px solid #ececec}
.promo-2{left:311px;background:linear-gradient(135deg,#2a2233,#4e2b2a 60%,#1d1d25)}
.promo-3{left:551px;background:linear-gradient(135deg,#3b3328,#6b5537 55%,#2a2520)}
.promo h3{position:absolute;left:16px;top:28px;width:200px;font-size:11px;font-weight:700;line-height:15px;letter-spacing:.3px}
.promo p{position:absolute;left:16px;top:62px;font-size:8px;color:#c9c9c9}
.btn-red{display:block;position:absolute;background:var(--red);color:var(--white);font-size:9px;font-weight:700;text-align:center;letter-spacing:.8px;line-height:24px;height:24px}
.promo .btn-red{left:16px;top:110px;width:78px}

.welcome{position:absolute;top:585px;left:0;width:853px;height:150px;text-align:center}
.welcome h2{margin-top:8px;font-size:22px;color:#2a2a2a;font-weight:800}
.welcome p{width:600px;margin:8px auto 0;font-size:10px;line-height:15px;color:var(--text)}
.welcome .btn-red{left:383px;top:88px;width:88px}

.festive{position:absolute;top:735px;left:0;width:853px;height:290px;background:linear-gradient(180deg,#0a0b12 0%,#161b2c 60%,#0d0f16 100%)}
.festive h2{position:absolute;top:104px;width:100%;text-align:center;color:var(--white);font-size:25px;font-weight:700}
.festive p{position:absolute;top:140px;left:260px;width:333px;text-align:center;color:#d8d8e0;font-size:10px;line-height:14px}
.festive .btn-red{left:383px;top:188px;width:88px}
.dots{position:absolute;top:234px;left:0;width:100%;display:flex;justify-content:center;gap:6px}
.dots i{width:6px;height:6px;border-radius:50%;background:#777}
.dots i.on{background:var(--white)}

.site-footer{position:absolute;top:1025px;left:0;width:853px;height:175px;background:var(--dark);color:var(--white)}
.footer-col{position:absolute;top:22px}
.footer-col h4{font-size:11px;font-weight:700;letter-spacing:.8px;margin-bottom:12px}
.footer-col li{list-style:none;font-size:8px;color:#bdbdbd;line-height:15px;letter-spacing:.4px}
.quick{left:71px}
.contact{left:311px}
.contact .addr{font-size:8px;color:#bdbdbd;line-height:14px}
.contact .phone{font-size:13px;font-weight:800;margin:4px 0}
.follow{left:632px}
.follow .social{position:static}
.copyright{position:absolute;right:72px;bottom:14px;font-size:7px;color:#8c8c8c}
</style>
</head>
<body>
<div class="page">

  <header class="site-header">
    <div class="brand">
      <div class="brand-name">MARROWIND</div>
      <div class="brand-tag">FIREWORKS &amp; PYROTECHNICS</div>
    </div>
    <div class="search">SEARCH</div>
    <div class="cart">
      <svg width="11" height="10" viewBox="0 0 11 10"><path d="M0 1h2l1.5 6h6L11 3H3" fill="none" stroke="#d7141a" stroke-width="1.3"/><circle cx="4" cy="9" r="1" fill="#d7141a"/><circle cx="9" cy="9" r="1" fill="#d7141a"/></svg>
      SHOPPING CART
    </div>
    <div class="social"><span></span><span></span><span></span></div>
  </header>

  <nav class="main-nav">
    <a class="active">FOUNTAINS</a>
    <a>ROMAN CANDLES</a>
    <a>ROCKETS</a>
    <a>FIRECRACKERS</a>
    <a>ASSORTMENTS</a>
  </nav>

  <section class="hero" role="img" aria-label="Crowd with raised hands at a night concert under purple and red stage lights">
    <svg class="hero-arrow" style="left:20px" width="14" height="24" viewBox="0 0 14 24"><path d="M12 2L2 12l10 10" fill="none" stroke="#fff" stroke-width="2"/></svg>
    <svg class="hero-arrow" style="right:20px" width="14" height="24" viewBox="0 0 14 24"><path d="M2 2l10 10L2 22" fill="none" stroke="#fff" stroke-width="2"/></svg>
    <h1 class="hero-title">MARROWIND FIREWORKS &amp; PYROTECHNICS</h1>
    <p class="hero-text">Bright nights and bold colour for every crowd, from harbour shows to private parties, planned and fired by a licensed crew.</p>
    <div class="btn-outline">SHOP NOW</div>
  </section>

  <div class="promo-band"></div>
  <div class="promo promo-1">
    <h3>FREE SHIPPING<br>ON ORDERS OVER $ 60</h3>
    <p>Fast delivery across the metro area</p>
    <span class="btn-red">SHOP NOW</span>
  </div>
  <div class="promo promo-2" role="img" aria-label="Fireworks over a theatre stage">
    <h3>PUBLIC DISPLAY, TV, THEATRICAL FIREWORKS</h3>
    <p>Shows built for stage and screen</p>
    <span class="btn-red">SHOP NOW</span>
  </div>
  <div class="promo promo-3" role="img" aria-label="Sparklers at a wedding celebration">
    <h3>WEDDINGS, CLUBS AND DO NICE SPECIAL FIREWORKS</h3>
    <p>Make your big day shine</p>
    <span class="btn-red">SHOP NOW</span>
  </div>

  <section class="welcome">
    <h2>WELCOME TO OUR WEBSITE</h2>
    <p>We design and fire custom shows for weddings, clubs, councils, film sets and any event that wants a moment to remember. Tell us your date and we will do the rest.</p>
    <span class="btn-red">GET STARTED</span>
  </section>

  <section class="festive" role="img" aria-label="Fireworks bursting over a harbour city skyline at night">
    <h2>CELEBRATE YOUR FESTIVE</h2>
    <p>Light up the holidays with a show made for your crowd, timed to music and fired safely by our team.</p>
    <span class="btn-red">SHOP NOW</span>
    <div class="dots"><i></i><i class="on"></i><i></i></div>
  </section>

  <footer class="site-footer">
    <div class="footer-col quick">
      <h4>QUICK LINKS</h4>
      <ul>
        <li>FOUNTAINS</li>
        <li>ROMAN CANDLES</li>
        <li>ROCKETS</li>
        <li>FIRECRACKERS</li>
        <li>ASSORTMENTS</li>
      </ul>
    </div>
    <div class="footer-col contact">
      <h4>CONTACT US</h4>
      <div class="addr">14 HARBOUR LANE, PYRMONT NSW 2009</div>
      <div class="phone">FREEPHONE: +1 800 472 913</div>
      <div class="addr">hello@tovellafireworks.com</div>
    </div>
    <div class="footer-col follow">
      <h4>FOLLOW US</h4>
      <div class="social"><span></span><span></span><span></span></div>
    </div>
    <div class="copyright">© 2024 tovellafireworks.com | Privacy Policy</div>
  </footer>

</div>
</body>
</html>
```